I would like a single page website for Skyward Rentals Pacific. In the file list provided there is basic information to be included as well as our logo with colors, fonts and images to be included.
Site must be very simple and be able to be loaded onto smart phones etc very quickly.
Site needs to be very smart in appearance

Target Market(s)

All prospective drone customers from Police to Parties.

Industry/Entity Type

Hire

Requirements
Must have
• Must have variation of color schemes supplied
Nice to have
• Must be very eye catching without going over the top
Should not have
• Anything slow to load.

```html
<!DOCTYPE html>
<html lang="en">
<head>
<meta charset="utf-8">
<title>Skyward Rentals Pacific</title>
<link href="https://fonts.googleapis.com/css2?family=Barlow:ital,wght@0,400;0,500;0,600;1,400&display=swap" rel="stylesheet">
<style>
:root{
  --green:#6aa324;
  --green-bright:#8dd62a;
  --green-text:#7cbf2c;
  --ink:#444;
  --muted:#8a8a8a;
  --light:#f2f2f2;
  --line:#e2e2e2;
  --footer:#3b3b3b;
  --white:#fff;
}
*{margin:0;padding:0;box-sizing:border-box}
html,body{width:795px;height:1200px;overflow:hidden;background:var(--white)}
body{font-family:"Barlow",Arial,sans-serif;color:var(--ink);position:relative}
.abs{position:absolute}
/* header */
.site-header{position:absolute;left:0;top:0;width:795px;height:67px;background:var(--white)}
.brand{left:66px;top:17px;display:flex;align-items:center;gap:6px}
.brand-mark{width:12px;height:12px;border-radius:50%;background:var(--green)}
.brand-name{font-size:14px;font-weight:600;color:var(--green);line-height:1.1;width:130px}
.main-nav{left:241px;top:28px;display:flex;font-size:8px;letter-spacing:.2px}
.main-nav a{color:var(--ink);text-decoration:none;text-transform:uppercase;margin-right:29px}
.main-nav a:last-child{margin-right:0}
.main-nav a.active{color:var(--green-text)}
.phone-btn{left:663px;top:19px;width:66px;height:24px;background:var(--green);color:var(--white);font-size:8.5px;display:flex;align-items:center;justify-content:center}
/* hero */
.hero{left:0;top:67px;width:795px;height:348px;background:linear-gradient(180deg,#5d7da8 0%,#7f9bbf 25%,#4c7a3c 55%,#6fb32a 80%,#8fd43a 100%)}
.hero-shade{left:0;top:0;width:795px;height:8px;background:linear-gradient(180deg,rgba(0,0,0,.35),transparent)}
.hero-title{left:64px;top:80px;font-size:23px;font-weight:600;color:var(--white);letter-spacing:.5px}
.hero-text{left:65px;top:124px;width:270px;font-size:11px;font-weight:500;line-height:16px;color:var(--white)}
.hero-btn{left:65px;top:203px;width:71px;height:29px;background:var(--green-bright);color:var(--white);font-size:8.5px;font-weight:600;display:flex;align-items:center;justify-content:center}
.hero-visual{left:372px;top:70px;width:373px;height:220px;border-radius:40px;background:radial-gradient(ellipse at center,rgba(235,235,235,.85) 0%,rgba(210,210,210,.5) 50%,rgba(255,255,255,0) 75%)}
.slider-dots{left:66px;top:297px;display:flex;gap:4px}
.slider-dots span{width:17px;height:2px;background:var(--white)}
.slider-dots span.off{background:#888}
/* services */
.services{left:0;top:415px;width:795px;height:251px;background:var(--light);border-bottom:1px solid var(--line)}
.arrow{top:108px}
.card{top:21px;width:150px;height:200px;background:var(--white);border:1px solid var(--line);text-align:center}
.card-photo{margin:6px 6px 0;height:97px}
.card h3{font-size:10px;font-weight:500;text-transform:uppercase;color:var(--ink);margin-top:8px;line-height:16px;letter-spacing:.3px}
.card p{font-size:7px;color:var(--muted);line-height:12.5px;padding:0 9px;margin-top:3px}
.card .btn{position:absolute;left:39px;top:174px;width:71px;height:25px;background:var(--green);color:var(--white);font-size:7.5px;display:flex;align-items:center;justify-content:center}
/* video */
.video-title{left:0;top:702px;width:795px;text-align:center;font-size:12.5px;font-weight:500;color:#555;letter-spacing:.2px}
.video-text{left:190px;top:728px;width:415px;text-align:center;font-size:7.5px;color:var(--muted);line-height:12.5px}
.video-frame{left:211px;top:766px;width:373px;height:145px;background:linear-gradient(180deg,#6b86b4 0%,#a9bbd6 50%,#5d78a8 100%)}
.play{left:383px;top:824px}
.divider{left:66px;top:940px;width:663px;height:1px;background:var(--line)}
/* info */
.col-title{top:972px;font-size:12px;font-weight:500;text-transform:uppercase;color:#555}
.welcome p{font-size:7.5px;color:var(--muted);line-height:13.5px;width:240px;margin-bottom:13px}
.who{list-style:none}
.who li{font-size:7.5px;color:var(--muted);height:16.6px;display:flex;align-items:center;gap:7px}
.quote{font-size:8.5px;font-style:italic;color:var(--green-text);line-height:13.5px;width:145px}
.quote-mark{font-size:20px;color:#777;font-style:normal;font-weight:600;line-height:0;vertical-align:-6px;margin-right:4px}
.quote-by{font-size:7.5px;color:var(--ink);margin-top:7px}
/* footer */
.site-footer{left:0;top:1148px;width:795px;height:52px;background:var(--footer)}
.social{left:66px;top:14px;display:flex;gap:3px}
.social span{width:23px;height:23px;border:1.5px solid var(--white);border-radius:50%;display:flex;align-items:center;justify-content:center}
.social span i{width:5px;height:5px;background:var(--white);border-radius:50%}
.copyright{right:66px;top:20px;font-size:7.5px;color:#ddd}
</style>
</head>
<body>
<header class="site-header">
  <div class="abs brand"><span class="brand-mark"></span><span class="brand-name">SKYWARD RENTALS PACIFIC</span></div>
  <nav class="abs main-nav">
    <a class="active" href="#">Home</a>
    <a href="#">About Us</a>
    <a href="#">Services</a>
    <a href="#">Projects</a>
    <a href="#">News</a>
    <a href="#">Video</a>
    <a href="#">Contact Us</a>
  </nav>
  <div class="abs phone-btn">0400 217 395</div>
</header>

<section class="abs hero" role="img" aria-label="Blurred green meadow and mountain sky backdrop">
  <div class="abs hero-shade"></div>
  <h1 class="abs hero-title">SKYWARD RENTALS PACIFIC</h1>
  <p class="abs hero-text">Lorem ipsum dolor sit amet, consectetur adipiscinsed eiusmod tempor incididunt ut labore et dolore magna aliquaenim ad minim veniamquis nostrud exercitation ullamco laboris.</p>
  <div class="abs hero-btn">READ MORE</div>
  <div class="abs hero-visual" role="img" aria-label="White quadcopter camera drone"></div>
  <div class="abs slider-dots"><span></span><span class="off"></span><span></span><span></span></div>
</section>

<section class="abs services">
  <svg class="abs arrow" style="left:18px" width="14" height="34"><polyline points="13,1 1,17 13,33" fill="none" stroke="#ccc" stroke-width="1"/></svg>
  <svg class="abs arrow" style="left:763px" width="14" height="34"><polyline points="1,1 13,17 1,33" fill="none" stroke="#ccc" stroke-width="1"/></svg>
  <article class="abs card" style="left:65px">
    <div class="card-photo" role="img" aria-label="Friends toasting at a celebration" style="background:linear-gradient(135deg,#7a6a55,#c9b79c 50%,#5a4a3c)"></div>
    <h3>Special Occasions</h3>
    <p>Lorem ipsum dolor sit amet, cons ectetur adipiscinsed eiusmod tempor incididunt ut labore et dolore.</p>
    <div class="btn">READ MORE</div>
  </article>
  <article class="abs card" style="left:237px">
    <div class="card-photo" role="img" aria-label="Children at a birthday party" style="background:linear-gradient(135deg,#d9a0b8,#e8c89a 50%,#6aa0c8)"></div>
    <h3>Childrens Birthday<br>Parties</h3>
    <p>Lorem ipsum dolor sit amet, cons ectetur adipiscinsed eiusmod</p>
    <div class="btn">READ MORE</div>
  </article>
  <article class="abs card" style="left:408px">
    <div class="card-photo" role="img" aria-label="Bride and groom with a bicycle outdoors" style="background:linear-gradient(135deg,#5f7a3a,#b8c2a0 50%,#4a5a30)"></div>
    <h3>Weddings</h3>
    <p>Lorem ipsum dolor sit amet, cons ectetur adipiscinsed eiusmod tempor incididunt ut labore et dolore.</p>
    <div class="btn">READ MORE</div>
  </article>
  <article class="abs card" style="left:579px">
    <div class="card-photo" role="img" aria-label="Surveillance drone on grass" style="background:linear-gradient(180deg,#8fa9c0,#6d8a4a 55%,#4f6a30)"></div>
    <h3>Surveillance</h3>
    <p>Lorem ipsum dolor sit amet, cons ectetur adipiscinsed eiusmod tempor incididunt ut labore et dolore.</p>
    <div class="btn">READ MORE</div>
  </article>
</section>

<h2 class="abs video-title">SPORTING EVENTS - 4K &nbsp;VIDEO OF YOURSELF PARTICIPATING IN MARATHONS ETC</h2>
<p class="abs video-text">Lorem ipsum dolor sit amet, consectetur adipiscing elit, sed do eiusmod tempor incididunt ut labore et dolore magna aliquat enim ad minim veniam, quis nostrud exercitation ullamc</p>
<div class="abs video-frame" role="img" aria-label="Video still of a hexacopter drone in the sky"></div>
<svg class="abs play" width="30" height="30" aria-label="Play video"><circle cx="15" cy="15" r="14" fill="rgba(0,0,0,.35)" stroke="#fff" stroke-width="1.5"/><polygon points="12,9.5 21,15 12,20.5" fill="#fff"/></svg>

<div class="abs divider"></div>

<h2 class="abs col-title" style="left:66px">Welcome to our site!!</h2>
<div class="abs welcome" style="left:66px;top:1001px">
  <p>Lorem ipsum dolor sit amet, consectetur adipiscing elit, sed do eiusmod tempor incididunt ut labore et dolore magna aliquat enim ad minim veniam, quis nostrud exercitation ullamc.</p>
  <p>Lorem ipsum dolor sit amet, consectetur adipiscing elit, sed do eiusmod tempor incididunt ut labore et dolore magna aliquaenim ad minim veniam, quis nostrud exercitation ullamc.</p>
</div>

<h2 class="abs col-title" style="left:341px">Who we are!!</h2>
<ul class="abs who" style="left:343px;top:996px">
  <li><svg width="9" height="9"><circle cx="4.5" cy="4.5" r="4" fill="none" stroke="#6aa324" stroke-width="1.3"/><polyline points="3.2,2.6 5,4.5 3.2,6.4" fill="none" stroke="#6aa324" stroke-width="1.3"/></svg>Real Estate Brochures</li>
  <li><svg width="9" height="9"><circle cx="4.5" cy="4.5" r="4" fill="none" stroke="#6aa324" stroke-width="1.3"/><polyline points="3.2,2.6 5,4.5 3.2,6.4" fill="none" stroke="#6aa324" stroke-width="1.3"/></svg>Construction project updates for remote stake holders</li>
  <li><svg width="9" height="9"><circle cx="4.5" cy="4.5" r="4" fill="none" stroke="#6aa324" stroke-width="1.3"/><polyline points="3.2,2.6 5,4.5 3.2,6.4" fill="none" stroke="#6aa324" stroke-width="1.3"/></svg>Surveillance – Police, Local councils worksafe etc</li>
  <li><svg width="9" height="9"><circle cx="4.5" cy="4.5" r="4" fill="none" stroke="#6aa324" stroke-width="1.3"/><polyline points="3.2,2.6 5,4.5 3.2,6.4" fill="none" stroke="#6aa324" stroke-width="1.3"/></svg>Building/Roof Condition Inspections</li>
  <li><svg width="9" height="9"><circle cx="4.5" cy="4.5" r="4" fill="none" stroke="#6aa324" stroke-width="1.3"/><polyline points="3.2,2.6 5,4.5 3.2,6.4" fill="none" stroke="#6aa324" stroke-width="1.3"/></svg>Lost pets</li>
  <li><svg width="9" height="9"><circle cx="4.5" cy="4.5" r="4" fill="none" stroke="#6aa324" stroke-width="1.3"/><polyline points="3.2,2.6 5,4.5 3.2,6.4" fill="none" stroke="#6aa324" stroke-width="1.3"/></svg>Accident reconstructions</li>
  <li><svg width="9" height="9"><circle cx="4.5" cy="4.5" r="4" fill="none" stroke="#6aa324" stroke-width="1.3"/><polyline points="3.2,2.6 5,4.5 3.2,6.4" fill="none" stroke="#6aa324" stroke-width="1.3"/></svg>Insurance assessing</li>
</ul>

<h2 class="abs col-title" style="left:588px">What customer says</h2>
<div class="abs" style="left:588px;top:1001px">
  <p class="quote"><span class="quote-mark">“</span>Lorem ipsum dolor sit amet, consectetur adipiscing elit, sed do eiusmod tempor incididunt ut labore et dolore magna aliqua. Ut enim ad minim veniam, quis nostrud exercitation ullamc.</p>
  <p class="quote-by">Alex Reed, City name</p>
</div>

<footer class="abs site-footer">
  <div class="abs social"><span><i></i></span><span><i></i></span><span><i></i></span><span><i></i></span><span><i></i></span></div>
  <p class="abs copyright">© 2015 all copyrights are reserved skywardrentalspacific.com.au</p>
</footer>
</body>
</html>
```